Corporate Business Card

Very professional, Modern, Not to busy, include phone address email, website
(253) 617-4930, 18761 52nd Avenue S, Kent, WA 98047, martin@plumlinegroup.com, varkoworks.com

Target Market(s)

Manufacturing

Industry/Entity Type

Aero, machining, manufacturing, Off road racing

Contact Information for Business Card

Phone, address email, website

```html
<!DOCTYPE html>
<html lang="en">
<head>
<meta charset="utf-8">
<title>Varko Works – Business Card</title>
<link rel="stylesheet" href="https://fonts.googleapis.com/css2?family=Lato:wght@400;700;900&family=Saira:wght@600&display=swap">
<style>
  :root {
    --backdrop: #232323;
    --navy-deep: #1f2d60;
    --navy-bright: #1a4788;
    --brand-red: #d0242b;
    --paper: #ffffff;
    --ink: #1c1c1c;
    --rule: #3a3a3a;
  }
  * { box-sizing: border-box; margin: 0; padding: 0; }
  html, body {
    width: 1200px; height: 895px; overflow: hidden;
    background: var(--backdrop);
  }
  .stage {
    width: 1200px; height: 895px;
    display: flex; flex-direction: column;
    align-items: center; justify-content: center;
    gap: 40px;
  }
  .card {
    width: 630px; height: 360px;
    position: relative;
    box-shadow: 0 10px 30px rgba(0,0,0,.45);
  }
  .card--front {
    background: linear-gradient(135deg, var(--navy-deep) 0%, var(--navy-deep) 45%, var(--navy-bright) 100%);
    display: flex; align-items: center; justify-content: center;
  }
  .brand {
    display: flex; flex-direction: column; align-items: flex-start;
  }
  .brand__row { display: flex; align-items: center; gap: 14px; }
  .brand__mark {
    width: 22px; height: 22px; background: var(--brand-red);
  }
  .brand__name {
    font-family: "Lato", sans-serif; font-weight: 900;
    font-size: 48px; letter-spacing: 3px; color: var(--paper);
    line-height: 1;
  }
  .brand__rule {
    margin-top: 16px; width: 150px; height: 2px; background: var(--paper);
  }
  .card--back { background: var(--paper); }
  .identity {
    position: absolute; right: 340px; top: 168px;
    text-align: right;
  }
  .identity__name {
    font-family: "Saira", sans-serif; font-weight: 600;
    font-size: 25px; letter-spacing: .5px; line-height: 1;
    text-transform: uppercase;
  }
  .identity__first { color: var(--navy-deep); }
  .identity__last { color: var(--brand-red); }
  .identity__title {
    font-family: "Lato", sans-serif; font-size: 16px;
    color: var(--ink); margin-top: 4px; letter-spacing: .4px;
  }
  .divider {
    position: absolute; left: 306px; top: 128px;
    width: 1.5px; height: 116px; background: var(--rule);
  }
  .contact {
    position: absolute; left: 326px; top: 130px;
    font-family: "Lato", sans-serif; font-size: 14px;
    line-height: 22px; color: var(--ink); list-style: none;
  }
  .contact__label { font-weight: 700; }
  .contact__web { color: var(--brand-red); font-weight: 700; }
</style>
</head>
<body>
  <main class="stage">
    <section class="card card--front" aria-label="Business card front">
      <div class="brand">
        <div class="brand__row">
          <span class="brand__mark"></span>
          <span class="brand__name">VARKO WORKS</span>
        </div>
        <span class="brand__rule"></span>
      </div>
    </section>

    <section class="card card--back" aria-label="Business card back">
      <div class="identity">
        <p class="identity__name"><span class="identity__first">Martin</span> <span class="identity__last">Hale</span></p>
        <p class="identity__title">Founder &amp; CEO</p>
      </div>
      <span class="divider"></span>
      <ul class="contact">
        <li>18761 52nd Avenue S, Kent</li>
        <li>WA 98047</li>
        <li><span class="contact__label">T:</span> (253) 617-4930</li>
        <li><span class="contact__label">E:</span> martin@plumlinegroup.com</li>
        <li class="contact__web">varkoworks.com</li>
      </ul>
    </section>
  </main>
</body>
</html>
```